Duct Manufacturing Company new to the industry needs business card and stationary design

we are sheet metal duct manufacturers looking for a business card design to fit my new business logo.
nothing to crazy that will date, but want it to stand out from the crowed.
I'm sure you guys will work it out.

Contact Information for Business Card

Glen Marsh
Director

Address
17 Dorwell St
Carrowdale NSW 2718

0438 760 514

Sales@flowbend.com.au

Font styles to use
Other font styles liked:
• BankGothic md bt

Requirements
Nice to have
• Like the idea of corner rounded to match logo
• like to keep colours flowing
• font I like sharp square not rounded

```html
<!DOCTYPE html>
<html lang="en">
<head>
<meta charset="utf-8">
<title>Flowbend Industries – Business Card</title>
<link href="https://fonts.googleapis.com/css2?family=Exo+2:wght@300;400;500;600&display=swap" rel="stylesheet">
<style>
  :root {
    --page-bg: #3b3b3b;
    --card-dark: #0b0b0b;
    --card-mid: #222223;
    --blue: #1c9ce0;
    --green: #8cc63f;
    --green-deep: #5fa532;
    --grey-band: #9a9a9a;
    --text-light: #c9c9c9;
    --rule: #6a6a6a;
  }
  * { box-sizing: border-box; margin: 0; padding: 0; }
  html, body {
    width: 1200px;
    height: 750px;
    overflow: hidden;
    background: var(--page-bg);
    font-family: "Exo 2", sans-serif;
  }
  .card {
    position: absolute;
    left: 100px;
    top: 90px;
    width: 1000px;
    height: 570px;
    overflow: hidden;
    background:
      linear-gradient(to bottom, var(--card-dark) 0%, var(--card-mid) 45%, #1a1a1b 100%);
  }
  .brand {
    position: absolute;
    right: 68px;
    top: 196px;
    text-align: right;
    color: var(--green);
    font-weight: 600;
    line-height: 1;
  }
  .brand-name {
    display: block;
    font-size: 50px;
    letter-spacing: 1px;
  }
  .brand-sub {
    display: block;
    margin-top: 6px;
    font-size: 31px;
    letter-spacing: 6px;
  }
  .person-name {
    position: absolute;
    left: 60px;
    top: 300px;
    font-size: 43px;
    font-weight: 600;
    color: var(--blue);
  }
  .person-role {
    position: absolute;
    left: 57px;
    top: 350px;
    font-size: 30px;
    font-weight: 400;
    color: var(--green);
  }
  .rule {
    position: absolute;
    left: 179px;
    top: 378px;
    width: 752px;
    height: 1px;
    background: var(--rule);
  }
  .contact-list {
    position: absolute;
    left: 60px;
    top: 404px;
    list-style: none;
  }
  .contact-item {
    display: flex;
    align-items: center;
    height: 38px;
    font-size: 23px;
    font-weight: 300;
    color: var(--text-light);
  }
  .contact-icon {
    width: 26px;
    height: 26px;
    margin-right: 14px;
    fill: var(--blue);
  }
  .address {
    position: absolute;
    right: 68px;
    top: 445px;
    text-align: right;
    font-style: normal;
    font-size: 23px;
    font-weight: 300;
    line-height: 37px;
    color: var(--text-light);
  }
  .base-band {
    position: absolute;
    left: 0;
    bottom: 0;
    width: 1000px;
    height: 19px;
  }
</style>
</head>
<body>
  <div class="card">
    <div class="brand">
      <span class="brand-name">FLOWBEND</span>
      <span class="brand-sub">INDUSTRIES</span>
    </div>

    <div class="person-name">Glen Marsh</div>
    <div class="person-role">Director</div>
    <div class="rule"></div>

    <ul class="contact-list">
      <li class="contact-item">
        <svg class="contact-icon" viewBox="0 0 24 24" aria-hidden="true"><path d="M6.6 10.8a15.2 15.2 0 0 0 6.6 6.6l2.2-2.2a1 1 0 0 1 1-.25 11.4 11.4 0 0 0 3.6.57 1 1 0 0 1 1 1V20a1 1 0 0 1-1 1A17 17 0 0 1 3 4a1 1 0 0 1 1-1h3.5a1 1 0 0 1 1 1c0 1.25.2 2.45.57 3.570a1 1 0 0 1-.25 1z"/></svg>
        0438 760 514
      </li>
      <li class="contact-item">
        <svg class="contact-icon" viewBox="0 0 24 24" aria-hidden="true"><path d="M2 5h20v14H2z M3.5 6.5 12 12.5l8.5-6" stroke="#1a1a1b" stroke-width="1.6"/></svg>
        Sales@flowbend.com.au
      </li>
      <li class="contact-item">
        <svg class="contact-icon" viewBox="0 0 24 24" aria-hidden="true"><circle cx="12" cy="12" r="10"/><path d="M7 6c2 1 3 3 2 5s1 3 3 3 1 3 0 5M15 4c-1 2 0 3 2 3s3 2 2 4" stroke="#1a1a1b" stroke-width="1.6" fill="none"/></svg>
        www.flowbend.com.au
      </li>
    </ul>

    <address class="address">
      17 Dorwell St<br>
      Carrowdale NSW 2718
    </address>

    <svg class="base-band" viewBox="0 0 1000 19" preserveAspectRatio="none" aria-hidden="true">
      <defs>
        <linearGradient id="band-green" x1="0" x2="1" y1="0" y2="0">
          <stop offset="0" stop-color="#5fa532"/>
          <stop offset="0.6" stop-color="#8cc63f"/>
          <stop offset="1" stop-color="#6fb336"/>
        </linearGradient>
      </defs>
      <polygon points="0,0 730,0 720,19 0,19" fill="url(#band-green)"/>
      <polygon points="736,0 838,0 828,19 726,19" fill="#1c9ce0"/>
      <polygon points="844,0 946,0 936,19 834,19" fill="#9a9a9a"/>
      <polygon points="952,0 1000,0 1000,19 942,19" fill="#8cc63f"/>
    </svg>
  </div>
</body>
</html>
```